Website Design - TallyPorchHelpers.net

PLEASE CHECK WORD DOCUMENT ATTACHED FOR WEBSITE FLOW.

Target Market(s)

REAL ESTATE AGENTS ARE THE TARGET MARKET

Industry/Entity Type

Real Estate

Coding

Coded - Design and coding required

Number of Pages Required

4 page

Colors

Designer to choose colors to be used in the design.

Requirements
Must have
• WE LIKE RED LOGO ATTACHED
Nice to have
• PLEASE CHECK WORD DOCUMENT ATTACHED FOR WEBSITE FLOW.
Should not have

```html
<!DOCTYPE html>
<html lang="en">
<head>
<meta charset="utf-8">
<title>Tally Porch Helpers — Open House Sign Services</title>
<link href="https://fonts.googleapis.com/css2?family=Rubik:wght@400;500;700&display=swap" rel="stylesheet">
<style>
:root{
  --red:#e8151f;
  --red-dark:#c10d18;
  --navy:#2b2b8e;
  --navy-deep:#262679;
  --purple-top:#86296f;
  --purple-bottom:#2d2e93;
  --ink:#222;
  --muted:#777;
  --paper:#f1f1f1;
  --white:#fff;
  --line:#dedede;
}
*{box-sizing:border-box;margin:0;padding:0}
html,body{width:1200px;height:3191px;overflow:hidden}
body{font-family:"Rubik",Arial,sans-serif;color:var(--ink);background:var(--white);position:relative}
section,header,footer{position:absolute;left:0;width:1200px}
.abs{position:absolute}

/* header */
.site-header{top:0;height:81px;background:var(--white)}
.brand{left:234px;top:22px;display:flex;align-items:center;gap:10px}
.brand-mark{width:34px;height:34px;background:var(--red)}
.brand-name{font-weight:700;font-size:17px;color:var(--navy);line-height:18px;width:110px}
.main-nav{left:405px;top:32px;display:flex;gap:22px;font-size:11px;font-weight:500;color:#444;text-transform:uppercase}
.header-phone{left:842px;top:24px;display:flex;gap:8px;align-items:center}
.header-phone small{display:block;font-size:10px;color:#666}
.header-phone strong{font-size:15px;color:var(--red)}

/* hero */
.hero{top:81px;height:519px}
.hero-photo{position:absolute;inset:0;background:linear-gradient(100deg,#a4472d 0%,#6a4a3a 35%,#3e3a35 70%,#2b2a28 100%)}
.hero-shade{position:absolute;inset:0;background:linear-gradient(180deg,rgba(0,0,0,.15),rgba(0,0,0,.35))}
.hero h1{position:absolute;top:214px;width:100%;text-align:center;color:var(--white);font-size:31px;font-weight:700}
.hero p{position:absolute;top:258px;width:100%;text-align:center;color:var(--white);font-size:17px;font-weight:500;line-height:23px}

/* options + how it works */
.options{top:600px;height:534px;background:var(--paper)}
.options-band{position:absolute;top:0;left:0;width:1200px;height:247px;background:linear-gradient(90deg,var(--red-dark),var(--red) 50%,var(--red-dark))}
.section-title{position:absolute;width:100%;text-align:center;font-weight:700;font-size:22px}
.options-title{top:44px;color:var(--white)}
.how-title{top:319px;color:#222}
.option-card{top:104px;width:230px;height:143px;background:var(--white);border-radius:4px;box-shadow:0 4px 14px rgba(0,0,0,.15);overflow:hidden;text-align:center}
.option-card svg.icon{margin-top:20px}
.option-card p{font-size:12px;font-weight:500;color:#333;margin-top:6px;line-height:15px;text-transform:uppercase}
.option-card svg.wave{position:absolute;bottom:0;left:0}
.step-num{width:42px;height:42px;border-radius:50%;background:var(--navy);color:var(--white);font-size:12px;font-weight:500;display:flex;align-items:center;justify-content:center;top:387px}
.step-text{top:437px;width:180px;text-align:center;font-size:11px;color:#666;line-height:15px}

/* service area */
.purple{background:linear-gradient(180deg,var(--purple-top),var(--purple-bottom))}
.service{top:1134px;height:413px}
.service .section-title{top:52px;color:var(--white)}
.service-item{top:119px;width:168px;color:var(--white)}
.service-photo{width:168px;height:135px;background:linear-gradient(160deg,#7aa05c,#c43a2e 55%,#5d7e9b)}
.service-item h3{font-size:12px;font-weight:500;margin-top:28px}
.service-item p{font-size:10.5px;line-height:16px;margin-top:10px;opacity:.8}

/* packages */
.packages{top:1547px;height:606px;background:#f4f4f4}
.packages .section-title{top:56px;color:#222}
.plan{top:119px;width:138px;height:419px;background:var(--white);box-shadow:0 3px 12px rgba(0,0,0,.13);border-radius:3px;text-align:center}
.plan-head{height:62px;background:#f1f1f1;font-size:13px;font-weight:500;padding-top:14px;position:relative}
.plan-featured .plan-head{background:var(--red);color:var(--white)}
.price{position:absolute;left:41px;top:36px;width:56px;height:56px;border-radius:50%;background:var(--red);color:var(--white);font-size:20px;font-weight:700;display:flex;align-items:center;justify-content:center}
.plan-featured .price{background:var(--navy)}
.price sup{font-size:10px}
.plan ul{list-style:none;text-align:left;padding:44px 12px 0 14px}
.plan li{display:flex;gap:5px;font-size:10px;color:#444;line-height:14px;margin-bottom:12px}
.plan li svg{flex:none;margin-top:2px}
.plan-btn{display:block;margin:4px auto 0;width:108px;height:40px;background:var(--navy);color:var(--white);font-size:10px;font-weight:500;line-height:40px;text-transform:uppercase}
.plan-featured .plan-btn{background:var(--red)}
.plan-btn.wide{line-height:13px;padding-top:7px;font-size:9px}
.plan-note{font-size:9px;color:#888;line-height:13px;margin-top:11px;padding:0 8px}

/* faq */
.faq{top:2153px;height:439px}
.faq .section-title{top:56px;color:var(--white)}
.faq-item{width:356px;height:34px;background:var(--white);font-size:12px;color:#333;display:flex;align-items:center;justify-content:space-between;padding:0 12px;border-left:3px solid var(--navy);white-space:nowrap}
.faq-item b{font-weight:400;font-size:16px;color:#555}
.faq-item.open{background:var(--red);color:var(--white);border-left-color:var(--red-dark)}
.faq-item.open b{color:var(--white)}
.faq-answer{width:356px;height:86px;background:var(--white);font-size:10.5px;color:#555;line-height:15px;padding:8px 12px}

/* news & testimonials */
.news{top:2592px;height:315px;background:var(--white)}
.testimonials{left:602px;top:0;width:598px;height:315px;background:linear-gradient(120deg,var(--red-dark),var(--red))}
.news h2,.testimonials h2{font-size:22px;font-weight:700;position:absolute;top:32px}
.news h2{left:234px}
.testimonials h2{left:26px;color:var(--white)}
.post{left:234px;width:350px;display:flex;gap:16px}
.post-photo{width:138px;height:88px;flex:none;background:linear-gradient(150deg,#9bb67b,#c9322b 60%,#6e8fa8)}
.post h3{font-size:12.5px;font-weight:500;color:#333;white-space:nowrap}
.post .meta{font-size:9.5px;color:#888;margin-top:5px}
.post .meta span{color:var(--red)}
.post p{font-size:10px;color:#888;line-height:14px;margin-top:6px}
.quote{left:26px;top:80px;width:340px;color:var(--white);font-size:10.5px;line-height:15.5px;display:flex;gap:10px}
.avatar{left:62px;top:240px;width:52px;height:52px;border-radius:50%;background:#e9d6cd;border:3px solid var(--white)}
.quote-name{left:124px;top:250px;color:var(--white);font-size:12px;font-weight:700}
.quote-name small{display:block;font-weight:400;font-size:10px;opacity:.85;margin-top:3px}
.dots{left:312px;top:285px;display:flex;gap:4px}
.dots i{width:7px;height:7px;border-radius:50%;border:1px solid var(--white)}
.dots i.on{background:var(--white)}

/* footer */
.site-footer{top:2907px;height:284px;background:var(--navy)}
.foot-col{top:40px;color:var(--white)}
.foot-col h4{font-size:11px;font-weight:500;text-transform:uppercase;margin-bottom:16px}
.foot-col p,.foot-col li{font-size:10.5px;line-height:15px;opacity:.8;list-style:none}
.foot-col li{margin-bottom:6px}
.socials{display:flex;gap:5px;margin-top:14px}
.socials i{width:24px;height:24px;border-radius:50%;border:1px solid rgba(255,255,255,.8)}
.field{width:170px;height:26px;background:var(--white);font-size:9.5px;color:#999;padding:7px 8px;margin-bottom:7px;border-radius:2px}
.field.tall{height:44px}
.send{width:170px;height:24px;background:var(--red);color:var(--white);font-size:10px;font-weight:500;text-align:center;line-height:24px;text-transform:uppercase}
.copyright{position:absolute;left:0;top:242px;width:1200px;height:42px;background:var(--navy-deep);color:var(--white);font-size:10.5px}
.copyright span{position:absolute;top:14px;opacity:.85}
</style>
</head>
<body>

<header class="site-header">
  <div class="brand abs"><span class="brand-mark"></span><span class="brand-name">Tally Porch Helpers</span></div>
  <nav class="main-nav abs"><span>How it works</span><span>Service Area</span><span>Pricing</span><span>About Us</span><span>FAQ</span>
    <svg width="12" height="12" viewBox="0 0 12 12"><circle cx="5" cy="5" r="3.5" fill="none" stroke="#444" stroke-width="1.6"/><path d="M7.6 7.6L11 11" stroke="#444" stroke-width="1.6"/></svg></nav>
  <div class="header-phone abs">
    <svg width="22" height="22" viewBox="0 0 24 24"><path d="M6.6 10.8a15 15 0 006.6 6.6l2.2-2.2a1 1 0 011-.25 11.4 11.4 0 003.6.57 1 1 0 011 1V20a1 1 0 01-1 1A17 17 0 013 4a1 1 0 011-1h3.5a1 1 0 011 1c0 1.25.2 2.45.57 3.57a1 1 0 01-.25 1z" fill="none" stroke="#e8151f" stroke-width="1.6"/></svg>
    <div><small>Call Or Text Us</small><strong>1-555-014-2290</strong></div>
  </div>
</header>

<section class="hero">
  <div class="hero-photo" role="img" aria-label="Real estate agent greeting a smiling couple outside a home with an open house sign on the lawn"></div>
  <div class="hero-shade"></div>
  <h1>Helping agents save time and money.</h1>
  <p>We place signs and boost foot traffic to your open houses<br>using proven marketing techniques.</p>
</section>

<section class="options">
  <div class="options-band"></div>
  <h2 class="section-title options-title">Choose The Option Below That Best Describes You</h2>

  <div class="option-card abs" style="left:234px">
    <svg class="icon" width="34" height="34" viewBox="0 0 34 34"><circle cx="17" cy="10" r="7" fill="#e8151f"/><path d="M4 32c0-8 6-12 13-12s13 4 13 12z" fill="#e8151f"/></svg>
    <p>I'm a<br>Full On Brokerage</p>
    <svg class="wave" width="230" height="22" viewBox="0 0 230 22"><path d="M0 8Q115 -4 230 10V22H0z" fill="#2b2b8e"/><path d="M0 14Q115 2 230 16V22H0z" fill="#e8151f"/></svg>
  </div>
  <div class="option-card abs" style="left:485px">
    <svg class="icon" width="40" height="34" viewBox="0 0 40 34"><circle cx="20" cy="9" r="6" fill="#e8151f"/><circle cx="8" cy="12" r="4.5" fill="#e8151f"/><circle cx="32" cy="12" r="4.5" fill="#e8151f"/><path d="M9 32c0-8 5-13 11-13s11 5 11 13z" fill="#e8151f"/><path d="M0 30c0-6 3-10 8-10 2 0 3 .5 4 1.2C9.5 24 8 27 8 30z" fill="#e8151f"/><path d="M40 30c0-6-3-10-8-10-2 0-3 .5-4 1.2 2.5 2.8 4 5.8 4 8.8z" fill="#e8151f"/></svg>
    <p>I'm an<br>Ind. Broker With A Team</p>
    <svg class="wave" width="230" height="22" viewBox="0 0 230 22"><path d="M0 8Q115 -4 230 10V22H0z" fill="#2b2b8e"/><path d="M0 14Q115 2 230 16V22H0z" fill="#e8151f"/></svg>
  </div>
  <div class="option-card abs" style="left:734px">
    <svg class="icon" width="34" height="34" viewBox="0 0 34 34"><rect x="5" y="3" width="24" height="3" fill="#e8151f"/><rect x="6" y="3" width="3" height="30" fill="#e8151f"/><rect x="25" y="3" width="3" height="30" fill="#e8151f"/><rect x="10" y="9" width="14" height="10" fill="#e8151f"/></svg>
    <p>I need<br>Sign Placement ASAP</p>
    <svg class="wave" width="230" height="22" viewBox="0 0 230 22"><path d="M0 8Q115 -4 230 10V22H0z" fill="#2b2b8e"/><path d="M0 14Q115 2 230 16V22H0z" fill="#e8151f"/></svg>
  </div>

  <h2 class="section-title how-title">How It Works</h2>
  <div class="step-num abs" style="left:328px">01</div>
  <div class="step-num abs" style="left:579px">02</div>
  <div class="step-num abs" style="left:830px">03</div>
  <svg class="abs" style="left:455px;top:401px" width="44" height="14" viewBox="0 0 44 14"><path d="M0 7H42M36 2l6 5-6 5" fill="none" stroke="#888" stroke-width="1.3"/></svg>
  <svg class="abs" style="left:706px;top:401px" width="44" height="14" viewBox="0 0 44 14"><path d="M0 7H42M36 2l6 5-6 5" fill="none" stroke="#888" stroke-width="1.3"/></svg>
  <p class="step-text abs" style="left:259px">Place signs strategically in best areas according to where the open house is located</p>
  <p class="step-text abs" style="left:510px">Pick Up the signs after the open house</p>
  <p class="step-text abs" style="left:761px">Store custom signs for you if needed</p>
</section>

<section class="service purple">
  <h2 class="section-title">Service Area</h2>
  <div class="service-item abs" style="left:234px"><div class="service-photo" role="img" aria-label="Red open house sign on a front lawn"></div><h3>Title Goes Here</h3><p>In publishing and graphic design, lorem ipsum is a placeholder text form of a document.</p></div>
  <div class="service-item abs" style="left:422px"><div class="service-photo" role="img" aria-label="Open house signs lined up along a street"></div><h3>Title Goes Here</h3><p>In publishing and graphic design, lorem ipsum is a placeholder text form of a document.</p></div>
  <div class="service-item abs" style="left:610px"><div class="service-photo" role="img" aria-label="Open house sign in front of a suburban home"></div><h3>Title Goes Here</h3><p>In publishing and graphic design, lorem ipsum is a placeholder text form of a document.</p></div>
  <div class="service-item abs" style="left:798px"><div class="service-photo" role="img" aria-label="Close view of a red open house sign"></div><h3>Title Goes Here</h3><p>In publishing and graphic design, lorem ipsum is a placeholder text form of a document.</p></div>
</section>

<section class="packages">
  <h2 class="section-title">Choose Your Package</h2>

  <div class="plan abs" style="left:234px"><div class="plan-head">5 SIGNS<div class="price"><sup>$</sup>49</div></div>
    <ul><li><svg width="9" height="9" viewBox="0 0 9 9"><path d="M1 4.5l2.3 2.3L8 1.5" fill="none" stroke="#2b2b8e" stroke-width="1.6"/></svg>Place signs strategically in best areas according to where the open house is located</li><li><svg width="9" height="9" viewBox="0 0 9 9"><path d="M1 4.5l2.3 2.3L8 1.5" fill="none" stroke="#2b2b8e" stroke-width="1.6"/></svg>Pick Up the signs after the open house</li><li><svg width="9" height="9" viewBox="0 0 9 9"><path d="M1 4.5l2.3 2.3L8 1.5" fill="none" stroke="#2b2b8e" stroke-width="1.6"/></svg>Store custom signs for you if needed</li></ul>
    <span class="plan-btn">Sign Up</span><p class="plan-note">Sign Up For A Subscription And Get These Marketing Services For Free</p></div>

  <div class="plan abs" style="left:383px"><div class="plan-head">10 SIGNS<div class="price"><sup>$</sup>59</div></div>
    <ul><li><svg width="9" height="9" viewBox="0 0 9 9"><path d="M1 4.5l2.3 2.3L8 1.5" fill="none" stroke="#2b2b8e" stroke-width="1.6"/></svg>Place signs strategically in best areas according to where the open house is located</li><li><svg width="9" height="9" viewBox="0 0 9 9"><path d="M1 4.5l2.3 2.3L8 1.5" fill="none" stroke="#2b2b8e" stroke-width="1.6"/></svg>Pick Up the signs after the open house</li><li><svg width="9" height="9" viewBox="0 0 9 9"><path d="M1 4.5l2.3 2.3L8 1.5" fill="none" stroke="#2b2b8e" stroke-width="1.6"/></svg>Store custom signs for you if needed</li></ul>
    <span class="plan-btn">Sign Up</span><p class="plan-note">Sign Up For A Subscription And Get These Marketing Services For Free</p></div>

  <div class="plan plan-featured abs" style="left:532px"><div class="plan-head">15 SIGNS<div class="price"><sup>$</sup>69</div></div>
    <ul><li><svg width="9" height="9" viewBox="0 0 9 9"><path d="M1 4.5l2.3 2.3L8 1.5" fill="none" stroke="#2b2b8e" stroke-width="1.6"/></svg>Place signs strategically in best areas according to where the open house is located</li><li><svg width="9" height="9" viewBox="0 0 9 9"><path d="M1 4.5l2.3 2.3L8 1.5" fill="none" stroke="#2b2b8e" stroke-width="1.6"/></svg>Pick Up the signs after the open house</li><li><svg width="9" height="9" viewBox="0 0 9 9"><path d="M1 4.5l2.3 2.3L8 1.5" fill="none" stroke="#2b2b8e" stroke-width="1.6"/></svg>Store custom signs for you if needed</li></ul>
    <span class="plan-btn">Sign Up</span><p class="plan-note">Sign Up For A Subscription And Get These Marketing Services For Free</p></div>

  <div class="plan abs" style="left:681px"><div class="plan-head">20 SIGNS<div class="price"><sup>$</sup>79</div></div>
    <ul><li><svg width="9" height="9" viewBox="0 0 9 9"><path d="M1 4.5l2.3 2.3L8 1.5" fill="none" stroke="#2b2b8e" stroke-width="1.6"/></svg>Place signs strategically in best areas according to where the open house is located</li><li><svg width="9" height="9" viewBox="0 0 9 9"><path d="M1 4.5l2.3 2.3L8 1.5" fill="none" stroke="#2b2b8e" stroke-width="1.6"/></svg>Pick Up the signs after the open house</li><li><svg width="9" height="9" viewBox="0 0 9 9"><path d="M1 4.5l2.3 2.3L8 1.5" fill="none" stroke="#2b2b8e" stroke-width="1.6"/></svg>Store custom signs for you if needed</li></ul>
    <span class="plan-btn">Sign Up</span><p class="plan-note">Sign Up For A Subscription And Get These Marketing Services For Free</p></div>

  <div class="plan abs" style="left:830px"><div class="plan-head">25+ SIGNS</div>
    <ul><li><svg width="9" height="9" viewBox="0 0 9 9"><path d="M1 4.5l2.3 2.3L8 1.5" fill="none" stroke="#2b2b8e" stroke-width="1.6"/></svg>Place signs strategically in best areas according to where the open house is located</li><li><svg width="9" height="9" viewBox="0 0 9 9"><path d="M1 4.5l2.3 2.3L8 1.5" fill="none" stroke="#2b2b8e" stroke-width="1.6"/></svg>Pick Up the signs after the open house</li><li><svg width="9" height="9" viewBox="0 0 9 9"><path d="M1 4.5l2.3 2.3L8 1.5" fill="none" stroke="#2b2b8e" stroke-width="1.6"/></svg>Store custom signs for you if needed</li></ul>
    <span class="plan-btn wide">Click Buy Now To<br>Create Custom Pkg</span><p class="plan-note">Sign Up For A Subscription And Get These Marketing Services For Free</p></div>
</section>

<section class="faq purple">
  <h2 class="section-title">Frequently Asked Questions</h2>
  <div class="faq-item abs" style="left:234px;top:112px">Vestibulum sed felis a ante suscipit auctor<b>+</b></div>
  <div class="faq-item abs" style="left:234px;top:157px">Sed ullamcorper augue ut facilisis condimentum<b>+</b></div>
  <div class="faq-item abs" style="left:234px;top:202px">Curabitur et ligula sed velit feugiat pellentesque<b>+</b></div>
  <div class="faq-item abs" style="left:234px;top:247px">Nam vitae velit non augue ultricies laoreet<b>+</b></div>

  <div class="faq-item abs" style="left:610px;top:112px">Curabitur et ligula sed velit feugiat pellentesque<b>+</b></div>
  <div class="faq-item open abs" style="left:610px;top:157px">Lorem Ipsum used in various languages for layouts<b>&minus;</b></div>
  <div class="faq-answer abs" style="left:610px;top:191px">In publishing and graphic design, lorem ipsum is a placeholder text commonly used to demonstrate the visual. In publishing and graphic design, lorem ipsum is a placeholder text commonly used to demonstrate the visual form of a document.</div>
  <div class="faq-item abs" style="left:610px;top:294px">Sed ullamcorper augue ut facilisis condimentum<b>+</b></div>
  <div class="faq-item abs" style="left:610px;top:337px">Nam vitae velit non augue ultricies laoreet<b>+</b></div>
</section>

<section class="news">
  <h2>Latest News</h2>
  <article class="post abs" style="top:80px"><div class="post-photo" role="img" aria-label="Open house sign on a lawn"></div>
    <div><h3>Lorem Ipsum charsets layouts</h3><p class="meta">By <span>Marta Quill</span> | 03 Aug 2018</p><p>Class aptent taciti sociosqu ad litora torquent per conubia nostra, per inceptos himenaeos. Mauris in erat justo.</p></div></article>
  <article class="post abs" style="top:192px"><div class="post-photo" style="background:linear-gradient(150deg,#6d8fb0,#c9b49a 55%,#4a6d3e)" role="img" aria-label="Agent shaking hands with a client"></div>
    <div><h3>Lorem Ipsum charsets layouts</h3><p class="meta">By <span>Marta Quill</span> | 03 Aug 2018</p><p>Class aptent taciti sociosqu ad litora torquent per conubia nostra, per inceptos himenaeos. Mauris in erat justo.</p></div></article>

  <div class="testimonials abs">
    <h2>Testimonials</h2>
    <div class="quote abs"><svg width="14" height="12" viewBox="0 0 14 12" style="flex:none"><path d="M0 12V6Q0 0 6 0v2Q3 2 3 6h3v6zM8 12V6q0-6 6-6v2q-3 0-3 4h3v6z" fill="#fff"/></svg>
      <p>Class aptent taciti sociosqu ad litora torquent per conubia nostra, per inceptos himenaeos. Mauris in condimentum elit amet a augue. Sed non neque elit. Sed ut imperdiet nisi. Proin condimentum fermentum nunc. Etiam pharetra, erat sed fermentum feugiat, velit mauris egestas quam, ut aliquam massa nisl quis neque. Suspendisse in orci enim. Mauris in condimentum sit amet a augue. Sed non fermentum feugiat, velit mauris egestas quam, neque elit.</p></div>
    <div class="avatar abs" role="img" aria-label="Client portrait"></div>
    <div class="quote-name abs">– Rowan Ellery<small>Lorem ipsum dolor</small></div>
    <div class="dots abs"><i class="on"></i><i></i><i></i><i></i><i></i></div>
  </div>
</section>

<footer class="site-footer">
  <div class="foot-col abs" style="left:234px;width:190px"><h4>About Tally Porch Helpers</h4>
    <p>Helping agents leverage their time and skills to increase production at an affordable price with impeccable support.</p>
    <div class="socials"><i></i><i></i><i></i><i></i><i></i></div></div>
  <div class="foot-col abs" style="left:464px;width:180px"><h4>Contact Information</h4>
    <p>8701 Lorem Ipsum Lane,<br>Suite 150, Doloro, TX 75000</p>
    <p style="margin-top:12px">Call Or Text Us:<br><strong style="font-size:13px;opacity:1">1-555-014-2290</strong></p>
    <p style="margin-top:12px">Email Us:<br>info@tallyporchhelpers.net</p></div>
  <div class="foot-col abs" style="left:670px"><h4>Quick Links</h4>
    <ul><li>How It Works</li><li>Service Area</li><li>Pricing</li><li>About Us</li><li>FAQ</li></ul></div>
  <div class="foot-col abs" style="left:796px"><h4>Quick Contact</h4>
    <div class="field">Your Name</div><div class="field">Email Address</div><div class="field tall">Message</div><div class="send">Send A Message</div></div>
  <div class="copyright"><span style="left:234px">Copyright © 2018 Tally Porch Helpers</span><span style="left:800px">Terms of Use | Privacy | Sitemap</span></div>
</footer>

</body>
</html>
```